Flat bootstrap design for existing site

I'm looking for a modern flat design based around an existing logo. This has to be a custom design (no external templates), and implemented into a bootstrap framework.

The logo is attached as 2 versions - choose whichever you want, that flows better with whatever design you choose.

Added screenshots of the existing site (currently using the default bootstrap layouts). Please make your designs around those pages in the screenshots (i.e. the homepage only has the postal code input and the header). The active page has 3 screenshots, because I wanted to illustrate the other states that would be visible (in the table rows).

This is a moving/junk removal website, just for some context.

Here's some example websites (flat designs) that I like, just to give you an idea of what I'm after.

https://www.plimvora.com/
https://dacklow.com/
https://trevanu.com/
https://quobrintal.com/en/

Coding

Coded - Design and coding required

Number of Pages Required

5+ page

Colors

Designer to choose colors to be used in the design.

Requirements
Must have
• It must be a modern/simple flat design, that is built around the existing logo (attached).
• It has to be implemented using bootstrap.

```html
<!DOCTYPE html>
<html lang="en">
<head>
<meta charset="utf-8">
<title>TROVEK – Booking details</title>
<link href="https://fonts.googleapis.com/css2?family=Rubik:wght@400;500;700&display=swap" rel="stylesheet">
<style>
:root{
  --sky:#38bdf2;
  --violet:#5f57c6;
  --heading:#5a56b2;
  --ink:#333;
  --muted:#555;
  --line:#e3e3e8;
  --page:#f6f6f6;
  --alert-bg:#d3ebf6;
  --alert-line:#a9d8ee;
  --badge:#d4d4dc;
  --white:#fff;
}
*{box-sizing:border-box;margin:0;padding:0}
html,body{width:1200px;height:872px;overflow:hidden}
body{font-family:"Rubik",sans-serif;background:var(--page);color:var(--ink);position:relative}
.site-header{position:absolute;left:0;top:0;width:1200px;height:78px;background:var(--sky)}
.brand{position:absolute;left:144px;top:22px;display:flex;align-items:center;gap:8px;color:var(--white);font-weight:700;font-size:28px;letter-spacing:1px}
.brand-dot{width:14px;height:14px;border-radius:50%;background:var(--white)}
.main-nav{position:absolute;right:144px;top:31px;display:flex;align-items:center;gap:26px;font-size:11.5px;font-weight:500;letter-spacing:.6px;color:var(--white)}
.main-nav .active{position:relative}
.main-nav .active::after{content:"";position:absolute;left:50%;margin-left:-6px;top:19px;width:12px;height:2px;background:var(--white)}
.account{display:flex;align-items:center;gap:6px;color:var(--violet);font-weight:400;font-size:12.5px;letter-spacing:.3px}
.avatar{width:18px;height:18px;border-radius:50%;background:var(--violet)}
.container{position:absolute;left:144px;width:912px}
h2{font-weight:400;color:var(--heading)}
.section-title{font-size:18px}
.field-label{position:absolute;font-size:12.5px;color:var(--ink)}
.input{position:absolute;height:36px;background:var(--white);border:1px solid var(--line);border-radius:3px;font-size:12.5px;color:#444;padding:10px 11px}
.input.focused{border-color:var(--violet)}
.cal{position:absolute;right:0;top:0;width:46px;height:34px;border-left:1px solid var(--line);display:flex;align-items:center;justify-content:center}
.btn{position:absolute;width:81px;height:36px;background:var(--violet);color:var(--white);font-size:11.5px;font-weight:700;letter-spacing:.8px;border-radius:2px;display:flex;align-items:center;justify-content:center}
.drivers-title{font-size:21px}
.alert{position:absolute;left:0;top:479px;width:912px;height:36px;background:var(--alert-bg);border:1px solid var(--alert-line);border-radius:3px;font-size:12.5px;color:#444;padding:10px 19px}
.panel{position:absolute;left:0;top:531px;width:912px;height:220px;background:var(--white);border:1px solid var(--line);border-radius:3px}
.table{position:absolute;left:16px;top:20px;width:880px;border-collapse:collapse;font-size:12.5px}
.table th{text-align:left;font-weight:500;height:27px;vertical-align:top;border-bottom:2px solid var(--line)}
.table td{height:41.6px;color:#444;border-bottom:1px solid var(--line)}
.table tr:last-child td{border-bottom:none}
.col-name{width:230px}.col-dist{width:259px}.col-time{width:195px;text-align:center}
.badge{display:inline-block;width:68px;height:17px;background:var(--badge);color:var(--white);font-size:11px;text-align:center;line-height:17px;margin-left:46px}
.fade{position:absolute;left:0;top:760px;width:1200px;height:46px;background:linear-gradient(var(--page),#ebebef)}
.site-footer{position:absolute;left:0;top:806px;width:1200px;height:59px;background:var(--white)}
.copy{position:absolute;left:144px;top:26px;font-size:12px;color:#444;letter-spacing:.3px}
.social{position:absolute;right:144px;top:21px;display:flex;gap:6px}
.social span{width:19px;height:19px;background:#8f8fb4;border-radius:2px}
.bottom-bar{position:absolute;left:0;top:865px;width:1200px;height:7px;background:var(--violet)}
</style>
</head>
<body>
<header class="site-header">
  <div class="brand"><span class="brand-dot"></span>TROVEK</div>
  <nav class="main-nav">
    <span>BOOK</span><span>HOW IT WORKS</span><span class="active">BECOME A DRIVER</span>
    <span class="account"><span class="avatar"></span>kestrel@mailvane.com
      <svg width="9" height="6" viewBox="0 0 9 6"><path d="M1 1l3.5 3.5L8 1" fill="none" stroke="currentColor" stroke-width="1.4"/></svg></span>
  </nav>
</header>

<main class="container" style="top:0;height:760px">
  <h2 class="section-title" style="position:absolute;top:129px">Booking details</h2>
  <label class="field-label" style="left:0;top:175px">Package selected:</label>
  <div class="input focused" style="left:0;top:196px;width:444px">Package 1</div>
  <label class="field-label" style="left:468px;top:175px">Pick-up time selected:</label>
  <div class="input" style="left:468px;top:196px;width:444px">July 18 at 4:13 am
    <span class="cal"><svg width="14" height="14" viewBox="0 0 14 14"><rect x="1" y="3" width="12" height="10" rx="1" fill="none" stroke="#5f57c6" stroke-width="1.6"/><rect x="1" y="3" width="12" height="3" fill="#5f57c6"/><path d="M4 1v3M10 1v3" stroke="#5f57c6" stroke-width="1.6"/></svg></span>
  </div>
  <label class="field-label" style="left:0;top:252px">Description:</label>
  <div class="input" style="left:0;top:272px;width:912px;height:76px">1 Large Stove</div>
  <div class="btn" style="left:0;top:363px">UPDATE</div>

  <h2 class="drivers-title" style="position:absolute;top:441px">Drivers in your area</h2>
  <div class="alert">Please stay on this page and be patient, while we contact the drivers and find you one ASAP.</div>
  <div class="panel">
    <table class="table">
      <thead><tr><th class="col-name">Name</th><th class="col-dist">Distance (KM)</th><th style="width:195px;text-align:left">Agreed pick-up time</th><th></th></tr></thead>
      <tbody>
        <tr><td>Dorran Pell</td><td>4.04 KM away</td><td class="col-time">-</td><td><span class="badge">Pending</span></td></tr>
        <tr><td>Ansel Morrow</td><td>5.07 KM away</td><td class="col-time">-</td><td><span class="badge">Pending</span></td></tr>
        <tr><td>Coby Lindqvist</td><td>11.13 KM away</td><td class="col-time">-</td><td><span class="badge">Pending</span></td></tr>
        <tr><td>Rafe Tolliver</td><td>11.91 KM away</td><td class="col-time">-</td><td><span class="badge">Pending</span></td></tr>
      </tbody>
    </table>
  </div>
</main>

<div class="fade"></div>
<footer class="site-footer">
  <p class="copy">© 2017 TROVEK. All rights reserved.</p>
  <div class="social"><span></span><span></span><span></span></div>
</footer>
<div class="bottom-bar"></div>
</body>
</html>
```